Lumen Fitness Personal Training Business

I need a business card design with a logo for my personal training company. I'd like the colors to be a vibrant green and black. I'd like the logo to incorporate an anvil (or something similar). I train hardcore competitive athletes as well as soccer moms trying to get and/or stay in shape. I need a logo that will not pigeon hole me in one category or the other, but at the same time not be too intimidating to soccer moms, but will not be off putting to the more hardcore trainees. The design should be attention grabbing and aesthetic.
Target Market(s)
Hardcore athletes as well as average people just trying to get/stay in shape.
Industry/Entity Type
Training

```html
<!DOCTYPE html>
<html lang="en">
<head>
<meta charset="utf-8">
<title>Lumen Fitness – Business Card</title>
<link href="https://fonts.googleapis.com/css2?family=Open+Sans:wght@400;600;700&display=swap" rel="stylesheet">
<style>
  :root {
    --backdrop: #2b2c30;
    --forest: #2f5e3a;
    --brand-green: #0ea34a;
    --light-green: #5cbf47;
    --ink: #3a3a3a;
    --paper: #ffffff;
  }
  * { box-sizing: border-box; margin: 0; padding: 0; }
  html, body {
    width: 1200px; height: 864px; overflow: hidden;
    background: var(--backdrop);
    font-family: "Open Sans", Arial, sans-serif;
  }
  .stage { position: relative; width: 1200px; height: 864px; }

  .card {
    position: absolute;
    width: 600px; height: 343px;
    overflow: hidden;
    box-shadow: 0 14px 30px rgba(0,0,0,.45);
  }

  /* Front */
  .card--front { left: 210px; top: 50px; background: var(--forest); }
  .front-brand {
    position: absolute; inset: 0;
    display: flex; align-items: center; justify-content: center; gap: 22px;
  }
  .brand-dot { width: 46px; height: 46px; border-radius: 50%; background: var(--paper); }
  .front-name {
    color: var(--paper); font-weight: 600; font-size: 44px;
    letter-spacing: 3px; text-transform: uppercase;
  }

  /* Back */
  .card--back { left: 300px; top: 440px; background: var(--paper); }
  .corner-mark { position: absolute; left: 0; top: 14px; }
  .person { position: absolute; left: 56px; top: 14px; }
  .person-name { color: var(--brand-green); font-weight: 700; font-size: 22px; line-height: 1.2; }
  .person-role { color: var(--ink); font-size: 14px; }

  .contact {
    position: absolute; left: 40px; top: 170px;
    color: var(--ink); font-size: 14px; line-height: 1.35;
  }
  .contact .address { margin-bottom: 10px; }
  .contact .label { color: var(--brand-green); }

  .back-brand {
    position: absolute; left: 300px; top: 150px;
    display: flex; align-items: center; gap: 14px;
  }
  .back-brand .brand-dot { width: 34px; height: 34px; background: var(--brand-green); }
  .back-name {
    color: var(--brand-green); font-weight: 600; font-size: 34px;
    letter-spacing: 2px; text-transform: uppercase;
  }

  .footer-bands { position: absolute; left: 0; bottom: 0; }
</style>
</head>
<body>
<main class="stage">

  <section class="card card--front" aria-label="Card front">
    <div class="front-brand">
      <span class="brand-dot"></span>
      <span class="front-name">Lumen Fitness</span>
    </div>
  </section>

  <section class="card card--back" aria-label="Card back">
    <svg class="corner-mark" width="44" height="42" viewBox="0 0 44 42">
      <polygon points="0,0 44,0 34,42 0,42" fill="var(--light-green)"/>
      <polygon points="20,0 44,0 34,42 6,42" fill="var(--brand-green)"/>
    </svg>
    <div class="person">
      <p class="person-name">Marcus Hale</p>
      <p class="person-role">Managing Director</p>
    </div>

    <div class="back-brand">
      <span class="brand-dot"></span>
      <span class="back-name">Lumen Fitness</span>
    </div>

    <address class="contact" style="font-style:normal">
      <p class="address">48 Harbor Lane<br>Westfield, 204817</p>
      <p><span class="label">p:</span> 044-555 210 347</p>
      <p><span class="label">f:</span> 044-555 210 348</p>
      <p><span class="label">e:</span> hello@lumenfit.com</p>
    </address>

    <svg class="footer-bands" width="600" height="80" viewBox="0 0 600 80">
      <polygon points="0,52 255,52 240,80 0,80" fill="var(--light-green)"/>
      <polygon points="262,38 600,38 600,80 246,80" fill="var(--brand-green)"/>
    </svg>
  </section>

</main>
</body>
</html>
```